Website for a Psychologist in Private Practice

I need a cool web design for my website: www.drkalvoric.com. I would like it to look professional. Keep all the current content and add: Space for video; radio spots (see Silver Cedar Tunes Logo below for those); Quick Inquiry; Friendora link; 5 star rating on Rivo; a map; reviews from former patients. I am open to suggestions.

Target Market(s)

Those seeking individual and marital counseling.

Industry/Entity Type

Mental Health

Number of Pages Required

1 page

Font styles to use
Sans Serif
Other font styles liked:
• I'm open but no hard to read script

Requirements
Must have
• All the content on my home page with link for video and radio spots. List services and degrees and expertices (pics not necessary).
Nice to have
• A video of me and radio conversations (logo of Silver Cedar Tunes radio attached).
Should not have
• Cartoons, comedy, etc.... I don't need pictures of services (marital, depression, etc...) Just list those.

```html
<!DOCTYPE html>
<html lang="en">
<head>
<meta charset="utf-8">
<title>Dr. Marla J. Kalvoric – Psychologist</title>
<link rel="stylesheet" href="https://fonts.googleapis.com/css2?family=Raleway:wght@400;600;700&family=Lato:wght@400;700&display=swap">
<style>
:root{
  --blue:#2b7bbb;
  --blue-dark:#1f5f94;
  --gold:#c9a94a;
  --gold-deep:#b8953a;
  --sand:#d8c688;
  --ink:#2b2b2b;
  --text:#555;
  --paper:#f3f3f3;
  --night:#050505;
  --footer:#232323;
  --footer-deep:#171717;
  --white:#fff;
}
*{box-sizing:border-box;margin:0;padding:0}
html,body{width:1200px;height:3082px;overflow:hidden}
body{font-family:'Lato',sans-serif;color:var(--text);background:var(--white);position:relative}
.abs{position:absolute}
h2{font-family:'Raleway',sans-serif;font-weight:700;color:var(--ink);font-size:31px;letter-spacing:.5px}
h2 span{color:var(--blue)}
.rule{display:block;width:36px;height:3px;background:var(--blue);margin-top:14px}
.btn{display:inline-block;background:var(--blue);color:var(--white);font-family:'Raleway',sans-serif;font-weight:700;font-size:14px;text-align:center;border-radius:2px}

/* top bar */
.topbar{top:0;left:0;width:1200px;height:41px;background:#2a2a2a;color:#ddd;font-size:12px}
.topbar .contact{left:100px;top:13px;display:flex;gap:28px}
.topbar .contact span::before{content:"";display:inline-block;width:10px;height:8px;background:var(--gold);margin-right:7px;vertical-align:0}
.topbar .social{right:40px;top:12px;display:flex;gap:16px;color:var(--gold);font-size:12px}

/* header */
.header{top:41px;left:0;width:1200px;height:95px;background:#f7f7f7}
.brand{left:100px;top:28px;font-family:'Lato',sans-serif;font-size:32px;color:var(--gold);font-weight:400}
.nav{left:556px;top:28px;display:flex;font-family:'Raleway',sans-serif;font-weight:700;font-size:14px;color:#222}
.nav a{padding:13px 14px;color:inherit;text-decoration:none}
.nav a.active{background:var(--blue);color:var(--white);border-radius:2px}

/* hero */
.hero{top:136px;left:0;width:1200px;height:462px;background:linear-gradient(100deg,#d7d3cc 0%,#efece6 35%,#cfc7bd 60%,#6e6660 100%)}
.hero .caption{left:0;bottom:0;width:1200px;height:47px;background:rgba(40,40,40,.55);color:var(--white);font-family:'Raleway',sans-serif;font-weight:600;font-size:26px;text-align:center;line-height:47px}
.hero .arrow{top:200px;width:30px;height:30px;background:#222;display:flex;align-items:center;justify-content:center}

/* about */
.portrait{top:598px;left:0;width:600px;height:485px;background:linear-gradient(135deg,#4f7a3a 0%,#87a860 40%,#c8b58c 60%,#3e6da0 100%)}
.about{top:598px;left:600px;width:600px;height:485px;background:var(--paper)}
.about-inner{left:37px;top:34px;width:520px}
.about h2 span{color:var(--gold)}
.about p{font-size:13.5px;line-height:22px;margin-top:12px}
.about .rule{margin-bottom:18px}
.about h3{font-family:'Raleway',sans-serif;color:var(--blue);font-size:15px;margin-top:14px;margin-bottom:6px}
.about li{list-style:none;font-size:12.5px;line-height:23px}
.about .btn{margin-top:14px;width:115px;height:39px;line-height:39px}

/* expertise */
.expertise{top:1083px;left:0;width:1200px;height:697px;background:var(--sand)}
.expertise .title{top:36px;width:1200px;text-align:center}
.expertise .title .rule{margin:14px auto 0}
.item{width:230px}
.item h4{font-family:'Raleway',sans-serif;font-weight:700;color:var(--blue-dark);font-size:16px;line-height:20px}
.item p{font-size:11.5px;color:#333;line-height:16px;margin-top:3px}
.item.right{text-align:right}

/* radio & video */
.media{top:1780px;left:0;width:1200px;height:520px;background:var(--night)}
.media h2{color:var(--white)}
.radio{left:100px;top:76px;width:450px}
.quote{margin-top:40px;color:#ddd;font-size:14px;line-height:23px}
.quote .mark{color:var(--gold);font-family:'Raleway',sans-serif;font-weight:700;font-size:24px;line-height:0}
.author{color:var(--gold);font-weight:700;font-size:15px;margin-top:18px}
.radio .btn{margin-top:68px;width:111px;height:39px;line-height:39px}
.video-title{left:615px;top:76px}
.video{left:615px;top:148px;width:585px;height:306px;background:linear-gradient(90deg,#a89e92 0%,#d8d0c4 40%,#8c8376 100%)}

/* sessions */
.booking{top:2339px;left:99px;width:326px;height:374px;border:5px solid #ddd;background:var(--white)}
.booking h3{text-align:center;font-family:'Raleway',sans-serif;font-weight:700;color:var(--blue);font-size:16px;margin-top:30px}
.field{position:absolute;left:27px;width:259px;height:33px;border:1px solid #d5d5d5;font-size:11px;color:#888;padding:10px 12px}
.field.half{width:122px}
.field .caret{position:absolute;right:10px;top:13px;width:0;height:0;border-left:5px solid transparent;border-right:5px solid transparent;border-top:6px solid var(--gold)}
.booking .btn{position:absolute;left:114px;top:297px;width:91px;height:35px;line-height:35px}
.sessions{top:2359px;left:483px;width:620px}
.sessions ul{margin-top:28px;list-style:none}
.sessions li{position:relative;padding-left:28px;font-size:13.5px;color:#333;line-height:19px;margin-bottom:14px}
.sessions li svg{position:absolute;left:0;top:1px}

/* footer */
.footer{top:2754px;left:0;width:1200px;height:283px;background:var(--footer);color:#ccc}
.footer h5{font-family:'Raleway',sans-serif;font-weight:700;font-size:17px;color:var(--white)}
.footer h5 span{color:var(--blue)}
.col{top:43px}
.links li{list-style:none;font-size:12px;line-height:30px;padding-left:12px;position:relative}
.links li::before{content:"";position:absolute;left:0;top:14px;width:3px;height:3px;background:#aaa;border-radius:50%}
.links li.active{color:var(--gold)}
.links li.active::before{background:var(--gold)}
.links{margin-top:14px}
.info{margin-top:14px;font-size:12px;line-height:18px}
.info .row{display:flex;gap:10px;margin-bottom:20px}
.info b{color:var(--white)}
.map{left:577px;top:74px;width:282px;height:113px;border:3px solid #fff;background:linear-gradient(135deg,#e9e6df 0%,#f6f3ec 50%,#d9e2e8 100%)}
.follow{display:flex;gap:14px;margin-top:16px}
.follow span{display:flex;align-items:center;gap:6px;font-size:12px;color:var(--white)}
.follow i{display:block;width:18px;height:18px;border-radius:50%;background:var(--blue)}
.donate{font-size:11px;font-weight:700;color:var(--white);line-height:14px;margin-top:22px;width:180px}
.badges{display:flex;gap:4px;margin-top:14px}
.badges i{display:block;width:80px;height:33px;background:#f4f4f4}
.copyright{top:3037px;left:0;width:1200px;height:45px;background:var(--footer-deep);color:#bbb;font-size:12px;text-align:center;line-height:45px}
</style>
</head>
<body>

<div class="abs topbar">
  <div class="abs contact"><span>mk@drkalvoric.com</span><span>(555) 210 4837</span></div>
  <div class="abs social"><span>Friendora</span><span>Chirpline</span></div>
</div>

<header class="abs header">
  <div class="abs brand">Dr. Marla J. Kalvoric</div>
  <nav class="abs nav">
    <a class="active">HOME</a><a>SESSIONS</a><a>MY EXPERTISE</a><a>RESOURCES</a><a>BIO</a><a>CONTACT US</a>
  </nav>
</header>

<section class="abs hero" role="img" aria-label="Photo of a couple in a counseling session with a therapist">
  <div class="abs arrow" style="left:10px"><svg width="10" height="12"><path d="M8 1 L2 6 L8 11" fill="none" stroke="#fff" stroke-width="2"/></svg></div>
  <div class="abs arrow" style="right:10px"><svg width="10" height="12"><path d="M2 1 L8 6 L2 11" fill="none" stroke="#fff" stroke-width="2"/></svg></div>
  <div class="abs caption">I am a phychologist providing individual and marital counseling</div>
</section>

<div class="abs portrait" role="img" aria-label="Portrait photo of Dr. Marla J. Kalvoric outdoors"></div>
<section class="abs about">
  <div class="abs about-inner">
    <h2>ABOUT <span>DR. MARLA J. KALVORIC</span></h2>
    <span class="rule"></span>
    <p>While I acknowledge the importance of my education, I also appreciate the role my experiences have played in allowing me to relate so well to others. Allow me to share those I feel are most relevant with you.</p>
    <p>I survived an abusive childhood that my mother and sister unfortunately did not.&nbsp; And it was my grief and desire to become stronger than my past that led me to counseling. A process that clearly changed my life</p>
    <h3>MY DEGREES</h3>
    <ul>
      <li>Doctoral Degree in Clinical Psychology</li>
      <li>Masters Degree in Counseling Psychology</li>
      <li>Doctoral Internship, Coastal University Medical Center</li>
      <li>Masters Internship, Westbrook Clinic</li>
    </ul>
    <span class="btn">READ MORE</span>
  </div>
</section>

<section class="abs expertise">
  <div class="abs title"><h2>MY <span>EXPERTISE</span></h2><span class="rule"></span></div>
  <svg class="abs" style="left:0;top:0" width="1200" height="697" viewBox="0 1083 1200 697">
    <g stroke="#8a94a0" stroke-width="1.5" fill="none">
      <line x1="569" y1="1461" x2="569" y2="1280"/><line x1="569" y1="1461" x2="707" y2="1367"/>
      <line x1="569" y1="1461" x2="707" y2="1562"/><line x1="569" y1="1461" x2="569" y2="1654"/>
      <line x1="569" y1="1461" x2="430" y2="1562"/><line x1="569" y1="1461" x2="430" y2="1367"/>
      <polyline points="420,1230 470,1230 520,1262"/>
      <polyline points="760,1352 870,1352"/>
      <polyline points="760,1562 820,1540 875,1540"/>
      <polyline points="600,1690 630,1693 735,1693"/>
      <polyline points="378,1562 340,1578 268,1578"/>
      <polyline points="378,1367 268,1358"/>
    </g>
    <g fill="#2b7bbb"><circle cx="870" cy="1352" r="3"/><circle cx="875" cy="1540" r="3"/><circle cx="268" cy="1578" r="3"/><circle cx="268" cy="1358" r="3"/></g>
    <g fill="#b8953a" stroke="#fbf6e4" stroke-width="7">
      <circle cx="569" cy="1280" r="53"/><circle cx="707" cy="1367" r="53"/><circle cx="707" cy="1562" r="53"/>
      <circle cx="569" cy="1654" r="53"/><circle cx="430" cy="1562" r="53"/><circle cx="430" cy="1367" r="53"/>
    </g>
    <circle cx="569" cy="1461" r="68" fill="#1f5f94" stroke="#fff" stroke-width="7"/>
    <text x="569" y="1457" text-anchor="middle" font-family="Lato,sans-serif" font-size="18" fill="#fff">Dr. Marla J.</text>
    <text x="569" y="1480" text-anchor="middle" font-family="Lato,sans-serif" font-size="18" fill="#fff">Kalvoric</text>
  </svg>
  <div class="abs item right" style="left:180px;top:133px"><h4>Dating</h4><p>Lorem ipsum dolor sit amensectetuer adipiscing elit, seddiam no</p></div>
  <div class="abs item right" style="left:32px;top:260px"><h4>Life Management</h4><p>Lorem ipsum dolor sit amensectetuer adipiscing elit,</p></div>
  <div class="abs item right" style="left:32px;top:482px"><h4>Personality Disorders</h4><p>Lorem ipsum dolor sit amensectetuer adipiscing elit,</p></div>
  <div class="abs item" style="left:877px;top:258px"><h4>Marriage</h4><p>Lorem ipsum dolor sit amensectetuer adipiscing elit, seddiam no</p></div>
  <div class="abs item" style="left:882px;top:443px"><h4>Parenting &amp; Professional Relationships</h4><p>Lorem ipsum dolor sit amensectetuer adipiscing elit, seddiam no</p></div>
  <div class="abs item" style="left:742px;top:598px;width:250px"><h4>Depression &amp; Anxiety Issues</h4><p>Lorem ipsum dolor sit amensectetuer adipiscing elit, seddiam no</p></div>
</section>

<section class="abs media">
  <div class="abs radio">
    <h2>RADIO <span>CONVERSATIONS</span></h2>
    <span class="rule"></span>
    <p class="quote"><span class="mark">“</span> Lorem ipsum dolor sit amet, consectetuer adipiscing elit, sed diam nonummy tincidunt ut laoreet dolore magna quam erat volutpat. Ut wisi enim ad minim veniam, quis nostrud exerci tation ullamcorper suscipit lobortis nisl ut aliquip ex ea commodo consequat. Duis autem vel eum iriure.laoreet dolore magna quam erat <span class="mark">”</span></p>
    <p class="author">Evan Marlow</p>
    <span class="btn">VIEW ALL</span>
  </div>
  <div class="abs video-title"><h2>VIEW <span>VIDEO</span></h2><span class="rule"></span></div>
  <div class="abs video" role="img" aria-label="Video still of a family counseling session">
    <svg class="abs" style="left:246px;top:125px" width="56" height="56"><circle cx="28" cy="28" r="25" fill="rgba(0,0,0,.25)" stroke="#fff" stroke-width="3"/><path d="M22 17 L38 28 L22 39 Z" fill="#fff"/></svg>
  </div>
</section>

<section class="abs booking">
  <h3>SCHEDULE AN APPOINTMENT</h3>
  <div class="field" style="top:91px">Full Name</div>
  <div class="field" style="top:143px">Phone Number</div>
  <div class="field half" style="top:192px">Date<i class="caret"></i></div>
  <div class="field half" style="top:192px;left:164px">Time<i class="caret"></i></div>
  <div class="field" style="top:243px">Location<i class="caret"></i></div>
  <span class="btn">SUBMIT</span>
</section>

<section class="abs sessions">
  <h2>MY <span>SESSIONS</span></h2>
  <span class="rule"></span>
  <ul>
    <li><svg width="16" height="14"><path d="M1 7 L6 12 L15 1" fill="none" stroke="#2b7bbb" stroke-width="3"/></svg>Individual sessions are 50 minutes in length</li>
    <li><svg width="16" height="14"><path d="M1 7 L6 12 L15 1" fill="none" stroke="#2b7bbb" stroke-width="3"/></svg>Marriage sessions are typically 50 to 75 minutes in length</li>
    <li><svg width="16" height="14"><path d="M1 7 L6 12 L15 1" fill="none" stroke="#2b7bbb" stroke-width="3"/></svg>Family sessions are 60 to 75 minutes in length</li>
    <li><svg width="16" height="14"><path d="M1 7 L6 12 L15 1" fill="none" stroke="#2b7bbb" stroke-width="3"/></svg>Divorce Mediation sessions are primarily conducted with individual sessions for each spouse with meetings as a couple kept to a minimum</li>
    <li><svg width="16" height="14"><path d="M1 7 L6 12 L15 1" fill="none" stroke="#2b7bbb" stroke-width="3"/></svg>Custody Evaluation sessions are usually initiated by each parties attorneys or the presiding judge</li>
    <li><svg width="16" height="14"><path d="M1 7 L6 12 L15 1" fill="none" stroke="#2b7bbb" stroke-width="3"/></svg>Testing sessions vary in length dependent upon the nature of the psychological assessment needed</li>
  </ul>
</section>

<footer class="abs footer">
  <div class="abs col" style="left:100px">
    <h5>Quick <span>Links</span></h5>
    <ul class="links"><li class="active">Home</li><li>Sessions</li><li>My Expertise</li><li>Resources</li><li>Bio</li><li>Contact Us</li></ul>
  </div>
  <div class="abs col" style="left:288px;width:260px">
    <h5>Contact <span>Details</span></h5>
    <div class="info">
      <div class="row"><svg width="12" height="16"><path d="M6 15 C2 9 1 7 1 5.5 A5 5 0 0 1 11 5.5 C11 7 10 9 6 15Z" fill="#ddd"/><circle cx="6" cy="5.5" r="2" fill="#232323"/></svg><div><b>Dr. Marla J. Kalvoric</b><br>418 Linden Court #120<br>Harbor Vale, CA 90000</div></div>
      <div class="row"><svg width="12" height="14"><path d="M2 1 L5 1 L6 4 L4 6 C5 8 6 9 8 10 L10 8 L12 9 L12 12 C6 13 1 8 2 1Z" fill="#ddd"/></svg>(555) 210 4837</div>
      <div class="row"><svg width="12" height="14"><rect x="2" y="0" width="8" height="14" rx="1.5" fill="#ddd"/><rect x="3.5" y="2" width="5" height="8" fill="#232323"/></svg>(555) 210 4837</div>
      <div class="row"><svg width="12" height="10"><rect x="0" y="1" width="12" height="8" fill="#ddd"/><path d="M0 1 L6 6 L12 1" fill="none" stroke="#232323"/></svg>mk@drkalvoric.com</div>
    </div>
  </div>
  <div class="abs col" style="left:577px"><h5>Location <span>Map</span></h5></div>
  <div class="abs map" role="img" aria-label="Street map of the office location"></div>
  <div class="abs col" style="left:939px">
    <h5>Follow <span>Us</span></h5>
    <div class="follow"><span><i></i>Friendora</span><span><i></i>Chirpline</span></div>
    <p class="donate">A portion of all revenue is donated to</p>
    <div class="badges"><i></i><i></i></div>
  </div>
</footer>
<div class="abs copyright">Copyright © 2016 Dr. Marla J. Kalvoric. All Rights Reserved</div>

</body>
</html>
```